Elegant Business Card with Logo and Picture

Please create a business card that has the Logo colors add Gold and turquoise / use the attached logo - I would like a beautiful Business Card - Please make sure it's printed on both sides / Picture can go on one side Logo other
www.velmoragrove.com
614-372-0583
Lina Suzette Brolin
linasb@quorvamail.com
Life Coach
Thessing Certified Teacher / Life Coach / Interior Designer
Transformational Retreats

Target Market(s)

Women Men General

Industry/Entity Type

Life Coaching

Contact Information for Business Card

www.velmoragrove.com
614-372-0583
Lina Suzette Brolin
Life Coach
Thessing Certified Teacher / Yoga Teacher / Interior Designer

Font styles to use
Serif
Decorative

Colors
33a6d6
e34197
ffc214

Requirements
Must have
• Quality Paper and touch /
Nice to have
• Beautiful Touch and feel
Should not have
• needs to be elegant

```html
<!DOCTYPE html>
<html lang="en">
<head>
<meta charset="utf-8">
<title>Lina Suzette Brolin – Business Card</title>
<link href="https://fonts.googleapis.com/css2?family=Roboto:wght@400;700&family=Roboto+Condensed:wght@400&family=Open+Sans:wght@400;600&family=Arvo:wght@400&display=swap" rel="stylesheet">
<style>
  :root {
    --bg: #e4e4e4;
    --card: #ffffff;
    --pink: #ff0a8c;
    --ink: #111111;
    --muted: #555555;
    --photo-a: #e9cf9a;
    --photo-b: #c98c6c;
  }
  html, body {
    margin: 0;
    width: 1200px;
    height: 1200px;
    overflow: hidden;
    background: var(--bg);
  }
  .card {
    position: absolute;
    left: 262px;
    width: 685px;
    height: 392px;
    background: var(--card);
    border-radius: 21px;
    overflow: hidden;
    box-shadow: 0 2px 6px rgba(0,0,0,0.12);
  }
  .card--front { top: 165px; }
  .card--back { top: 653px; }

  .portrait {
    position: absolute;
    left: 151px;
    top: 75px;
    width: 153px;
    height: 177px;
    border: 1px solid #999;
    border-radius: 13px;
    background: radial-gradient(circle at 50% 40%, var(--photo-a) 0%, var(--photo-b) 60%, #f3f0ee 100%);
    box-sizing: border-box;
  }
  .identity {
    position: absolute;
    left: 358px;
    top: 90px;
  }
  .identity__name {
    margin: 0 0 4px;
    font-family: "Roboto", sans-serif;
    font-weight: 700;
    font-size: 24px;
    color: var(--pink);
  }
  .identity__roles {
    margin: 0;
    font-family: "Roboto Condensed", sans-serif;
    font-size: 16px;
    line-height: 19.5px;
    color: var(--ink);
  }
  .contact {
    list-style: none;
    margin: 10px 0 0;
    padding: 0;
    font-family: "Open Sans", sans-serif;
    font-size: 16px;
    line-height: 22px;
    color: var(--muted);
  }
  .contact__item { display: flex; align-items: center; gap: 9px; }
  .contact__item svg { width: 13px; height: 13px; fill: var(--pink); }

  .band {
    position: absolute;
    left: 0;
    top: 318px;
    width: 100%;
    height: 41px;
    background: linear-gradient(to right, var(--ink) 0 608px, var(--pink) 608px);
  }
  .band__web {
    position: absolute;
    left: 0;
    width: 594px;
    top: 0;
    line-height: 41px;
    text-align: center;
    font-family: "Open Sans", sans-serif;
    font-size: 15px;
    letter-spacing: 2.2px;
    color: #fff;
  }
  .band__mark {
    position: absolute;
    left: 546px;
    top: 0;
    height: 41px;
    display: flex;
    align-items: center;
    gap: 6px;
    font-family: "Open Sans", sans-serif;
    font-weight: 600;
    font-size: 15px;
    color: #fff;
  }
  .band__dot {
    width: 8px;
    height: 8px;
    border-radius: 50%;
    background: var(--pink);
  }

  .brand {
    position: absolute;
    left: 0;
    width: 100%;
    top: 128px;
    text-align: center;
  }
  .brand__mark {
    display: inline-flex;
    align-items: center;
    gap: 12px;
    font-family: "Arvo", serif;
    font-size: 44px;
    line-height: 60px;
    color: var(--ink);
  }
  .brand__dot {
    width: 16px;
    height: 16px;
    border-radius: 50%;
    background: var(--pink);
  }
  .brand__name {
    margin: 42px 0 0;
    font-family: "Arvo", serif;
    font-size: 22px;
    letter-spacing: 3.6px;
    color: var(--ink);
    line-height: 26px;
  }
  .brand__tagline {
    margin: 0;
    font-family: "Open Sans", sans-serif;
    font-size: 11px;
    letter-spacing: 14px;
    padding-left: 14px;
    line-height: 14px;
    color: var(--pink);
  }
</style>
</head>
<body>

<section class="card card--front">
  <div class="portrait" role="img" aria-label="Portrait photograph of Lina Suzette Brolin"></div>
  <div class="identity">
    <h1 class="identity__name">Lina Suzette Brolin</h1>
    <p class="identity__roles">Life Coach<br>Thessing Certified Teacher /<br>Yoga Teacher / Interior Designer</p>
    <ul class="contact">
      <li class="contact__item">
        <svg viewBox="0 0 24 24" aria-hidden="true"><path d="M6.6 10.8c1.4 2.8 3.8 5.1 6.6 6.6l2.2-2.2c.3-.3.7-.4 1-.2 1.1.4 2.3.6 3.6.6.6 0 1 .4 1 1V20c0 .6-.4 1-1 1C10.6 21 3 13.4 3 4c0-.6.4-1 1-1h3.5c.6 0 1 .4 1 1 0 1.3.2 2.5.6 3.6.1.3 0 .7-.2 1L6.6 10.8z"/></svg>
        614-372-0583
      </li>
      <li class="contact__item">
        <svg viewBox="0 0 24 24" aria-hidden="true"><path d="M2 5h20v14H2z M3.5 6.5 12 13l8.5-6.5" stroke="#fff" stroke-width="1.5"/></svg>
        linasb@quorvamail.com
      </li>
    </ul>
  </div>
  <div class="band">
    <span class="band__web">www.velmoragrove.com</span>
    <span class="band__mark"><span class="band__dot"></span>Lina</span>
  </div>
</section>

<section class="card card--back">
  <div class="brand">
    <div class="brand__mark"><span class="brand__dot"></span>Lina</div>
    <p class="brand__name">VELMORA GROVE</p>
    <p class="brand__tagline">COACHING</p>
  </div>
</section>

</body>
</html>
```